Professional Business card

I need a business card to send with all my shipments. It needs to look very professional as I am branding myself, more than I am branding my company. The website is not active yet but that along with the instagram is very important as this will be moving shortly. The next required to be included is listed

Target Market(s)

All

Contact Information for Business Card

Very professional and sleek, I am trying to look like the CEO, motivational speaker and future president I plan to be

Colors
ffcf3e

Requirements
Must have
• Front

Dale Wrenfield
CEO
Brivolt Franchiser
Business Consultant/Start Up Guidance
Motivational Speaker
President of The United States 2040
www.dalewrenfield-example.com
[Instagram] @dalewrenfield

Back
I teach the success method used by my company you just bought from. Learn the unique model and start your own Brivolt franchise today
Nice to have
• Black and Gold lettering
Should not have
• Playful vibes

```html
<!DOCTYPE html>
<html lang="en">
<head>
<meta charset="UTF-8">
<title>Dale Wrenfield — Business Card</title>
<link href="https://fonts.googleapis.com/css2?family=Montserrat:wght@400;500;700&display=swap" rel="stylesheet">
<style>
  :root {
    --backdrop: #e4e4e2;
    --card-white: #fbfbfa;
    --card-black: #262626;
    --gold-on-white: #a88f56;
    --gold-on-black: #bf9f5c;
    --card-shadow: rgba(0, 0, 0, 0.14);
  }
  * { margin: 0; padding: 0; box-sizing: border-box; }
  html, body {
    width: 1200px;
    height: 800px;
    overflow: hidden;
    background: var(--backdrop);
    font-family: "Montserrat", sans-serif;
  }
  .canvas {
    width: 1200px;
    height: 800px;
    display: flex;
    align-items: center;
    justify-content: center;
    gap: 50px;
  }
  .card {
    width: 525px;
    height: 300px;
    border-radius: 2px;
    box-shadow: 0 6px 18px var(--card-shadow);
    display: flex;
    align-items: center;
    justify-content: center;
    text-align: center;
  }
  .card--front {
    background: var(--card-white);
    color: var(--gold-on-white);
  }
  .card--back {
    background: var(--card-black);
    color: var(--gold-on-black);
    padding: 0 56px;
  }
  .identity__name {
    font-weight: 700;
    font-size: 24px;
    letter-spacing: 0.5px;
    line-height: 1.1;
  }
  .identity__role {
    font-size: 16px;
    font-weight: 500;
    margin-bottom: 10px;
  }
  .identity__titles {
    list-style: none;
    font-size: 14.5px;
    line-height: 1.4;
    margin-bottom: 12px;
  }
  .identity__contact {
    font-size: 14.5px;
    line-height: 1.45;
  }
  .identity__social {
    display: inline-flex;
    align-items: center;
    gap: 6px;
  }
  .identity__social svg { width: 13px; height: 13px; }
  .pitch {
    font-size: 17px;
    line-height: 1.45;
    letter-spacing: 0.3px;
  }
  .pitch__mark {
    font-weight: 700;
    font-size: 26px;
    line-height: 0;
    vertical-align: -6px;
  }
</style>
</head>
<body>
  <main class="canvas">
    <section class="card card--front" aria-label="Card front">
      <div class="identity">
        <h1 class="identity__name">Dale Wrenfield</h1>
        <p class="identity__role">CEO</p>
        <ul class="identity__titles">
          <li>Brivolt Franchiser</li>
          <li>Business Consultant/Start Up Guidance</li>
          <li>Motivational Speaker</li>
          <li>President of The United States 2040</li>
        </ul>
        <p class="identity__contact">www.dalewrenfield-example.com</p>
        <p class="identity__contact identity__social">
          <svg viewBox="0 0 14 14" aria-hidden="true"><circle cx="7" cy="7" r="6" fill="none" stroke="currentColor" stroke-width="1.3"/></svg>
          @dalewrenfield
        </p>
      </div>
    </section>

    <section class="card card--back" aria-label="Card back">
      <p class="pitch">
        <span class="pitch__mark">“</span> I teach the success method used by my company you just bought from. Learn the unique model and start your own Brivolt franchise today <span class="pitch__mark">”</span>
      </p>
    </section>
  </main>
</body>
</html>
```